BWP Business Card

A double sided business card based on your "Brindlewood Partners Ltd" Logo. To use the "BWP" logo on 1 side and the full company logo on the reverse.

Detials to be included:

Name: Tomas Wheeler
Postion: Consultant Orthotist & Expert Witness
T: +44 (0) 7700 938271
F: +44 (0) 7654 8820

```html
<!DOCTYPE html>
<html lang="en">
<head>
<meta charset="utf-8">
<title>BWP Business Card</title>
<link href="https://fonts.googleapis.com/css2?family=Open+Sans:wght@400;700&display=swap" rel="stylesheet">
<style>
  :root {
    --navy: #1d3f78;
    --grey: #9b9b9b;
    --grey-light: #d9d9d9;
    --text-dark: #3a3a3a;
    --card: #ffffff;
    --backdrop: #eceae6;
  }
  * { margin: 0; padding: 0; box-sizing: border-box; }
  html, body { width: 1200px; height: 720px; overflow: hidden; }
  body {
    background: var(--backdrop);
    font-family: "Open Sans", Arial, sans-serif;
    position: relative;
  }
  .card {
    position: absolute;
    top: 205px;
    width: 540px;
    height: 309px;
    background: var(--card);
    box-shadow: 0 2px 10px rgba(0,0,0,0.12);
    overflow: hidden;
  }
  .card--front { left: 40px; }
  .card--back { left: 620px; }

  .company-name {
    font-family: "Open Sans", Arial, sans-serif;
    font-weight: 700;
    color: var(--navy);
    line-height: 1.1;
  }
  .tagline {
    font-family: "Open Sans", Arial, sans-serif;
    font-weight: 400;
    color: var(--grey);
  }

  /* Front brand block */
  .front-brand {
    position: absolute;
    top: 40px;
    left: 150px;
    display: flex;
    align-items: center;
    gap: 16px;
  }
  .front-brand__square {
    width: 52px; height: 52px;
    background: var(--navy);
  }
  .front-brand .company-name { font-size: 19px; }
  .front-brand .tagline { font-size: 9px; margin-top: 4px; }

  /* Front details */
  .person {
    position: absolute;
    top: 136px;
    right: 285px;
    text-align: right;
  }
  .person__name { font-size: 15px; font-weight: 700; color: var(--navy); }
  .person__role { font-size: 9.5px; color: var(--grey); margin-top: 1px; }
  .person__address { font-size: 9.5px; color: var(--text-dark); line-height: 1.35; margin-top: 2px; }
  .details-divider {
    position: absolute;
    top: 122px; left: 265px;
    width: 1px; height: 78px;
    background: var(--grey-light);
  }
  .contacts {
    position: absolute;
    top: 124px; left: 278px;
    list-style: none;
  }
  .contacts li {
    display: flex; align-items: center;
    font-size: 10px; color: var(--text-dark);
    height: 18px;
  }
  .contacts svg { width: 10px; height: 10px; margin-right: 6px; fill: var(--navy); }
  .front-band { position: absolute; left: 0; top: 0; width: 540px; height: 309px; }

  /* Back */
  .back-brand {
    position: absolute;
    inset: 0;
    display: flex; flex-direction: column;
    align-items: center; justify-content: center;
    text-align: center;
  }
  .back-brand .company-name { font-size: 36px; }
  .back-brand .tagline { font-size: 13px; margin-top: 12px; letter-spacing: 0.04em; }
</style>
</head>
<body>
  <section class="card card--front" aria-label="Business card front">
    <svg class="front-band" viewBox="0 0 540 309" aria-hidden="true">
      <path d="M0 262 Q 270 232 540 216" stroke="var(--grey)" stroke-width="2" fill="none"/>
      <path d="M0 274 Q 270 244 540 228 L540 309 L0 309 Z" fill="var(--navy)"/>
    </svg>

    <div class="front-brand">
      <div class="front-brand__square"></div>
      <div>
        <div class="company-name">Brindlewood<br>Partners Ltd</div>
        <div class="tagline">Clear Reports for Clinical Claims</div>
      </div>
    </div>

    <div class="person">
      <div class="person__name">Tomas Wheeler</div>
      <div class="person__role">Consultant Orthotist &amp; Expert Witness</div>
      <div class="person__address">18 Hollis Row Kingston<br>Surrey, KT2 4RW</div>
    </div>
    <div class="details-divider"></div>
    <ul class="contacts">
      <li><svg viewBox="0 0 10 10"><circle cx="5" cy="5" r="5"/><path d="M3 2.5h1.2l.5 1.3-.7.6a4 4 0 0 0 1.6 1.6l.6-.7 1.3.5V7a.6.6 0 0 1-.6.6A4.7 4.7 0 0 1 2.4 3.1.6.6 0 0 1 3 2.5z" fill="#fff"/></svg>+44 (0) 7700 938271</li>
      <li><svg viewBox="0 0 10 10"><rect x="2.5" y="1" width="5" height="3"/><rect x="0.5" y="4" width="9" height="4" rx="1"/><rect x="2.5" y="6.5" width="5" height="3"/></svg>+44 (0) 7654 8820</li>
      <li><svg viewBox="0 0 10 10"><rect x="0.5" y="2" width="9" height="6.5" rx="0.8"/><path d="M0.8 2.4 5 5.6 9.2 2.4" stroke="#fff" stroke-width="0.9" fill="none"/></svg>tomas@brindlewoodpartners.co.uk</li>
    </ul>
  </section>

  <section class="card card--back" aria-label="Business card back">
    <div class="back-brand">
      <div class="company-name">Brindlewood<br>Partners Ltd</div>
      <div class="tagline">Clear Reports for Clinical Claims</div>
    </div>
  </section>
</body>
</html>
```